New website for salon services and wedding hair and makeup

I am a professional hairstylist and makeup artist in Charleston, SC. I have my own company where I see clients for cut and color and I also go on site for weddings. I have a current website that I would like to update and change the style. I would like to add a contact form, map, additional pages and be mobile friendly. It is important to me that it have a site map and can show up in searches. I will need to add photos to the site every so often and would like to continue to work with the designer. I have a logo that I am happy with and have attached the file however if you think a new logo would help the look of the site I am open to it. My current website is www.brightcombstudio-example.com, I would like to change the style and layout so it looks up to date. Here are some links to sites that I like the look of but I don't want to limit your creativity. http://willowlanefolio-example.com/ http://www.runwaylensworks-example.com http://miraventhol-example.com/. I have attached a few files for mock up purposes, please let me know if you would like more content. Thank you!

Target Market(s)

Women, Brides

Industry/Entity Type

Hair And Beauty

Number of Pages Required

1 page

Font styles to use
Sans Serif
Script

Requirements
Must have
• Contact form, Mobile friendly, sitemap
Nice to have
• I really like the look for the sites I have included on the project description guide.
Should not have
• Nothing overly girly.

```html
<!DOCTYPE html>
<html lang="en">
<head>
<meta charset="utf-8">
<title>Brightcomb Studio – Hair and Makeup</title>
<link rel="stylesheet" href="https://fonts.googleapis.com/css2?family=Bebas+Neue&family=Great+Vibes&family=Open+Sans:wght@400;600;700&display=swap">
<style>
:root{
  --navy:#0d2f5a;
  --nav:#0b3c5f;
  --nav-active:#cfe6f2;
  --accent:#1f4f8a;
  --text:#555b63;
  --rule:#1c3f6b;
  --white:#ffffff;
  --field:#8ca4bd;
}
*{box-sizing:border-box;margin:0;padding:0}
html,body{width:1200px;height:3512px;overflow:hidden;background:var(--white)}
body{position:relative;font-family:"Open Sans",Arial,sans-serif;color:var(--text)}
.abs{position:absolute}

/* hero */
.hero{left:0;top:0;width:1200px;height:800px;background:linear-gradient(90deg,#dfe0e3 0%,#eceae6 50%,#d6d4d0 100%)}
.hero-boards{left:0;top:0;width:1200px;height:800px;background:repeating-linear-gradient(180deg,rgba(255,255,255,0) 0,rgba(255,255,255,0) 118px,rgba(150,150,155,.35) 118px,rgba(150,150,155,.35) 121px)}
.hero-photo{left:560px;top:0;width:440px;height:800px;background:radial-gradient(ellipse at 50% 12%,#c9a48a 0%,#c9a48a 8%,rgba(201,164,138,0) 16%),linear-gradient(180deg,#efe9df 0%,#e2d6c4 40%,#d2c2ab 70%,#c3b09a 100%)}
.hero-ribbon{left:760px;top:600px;width:440px;height:150px;background:linear-gradient(100deg,rgba(123,54,160,0) 0%,#8a3fb0 35%,#6b2b93 70%,#4e1f70 100%)}
.brand{left:80px;top:112px;font-weight:700;font-size:50px;color:var(--navy);letter-spacing:1px}
.hero-title{left:100px;top:332px;font-family:"Bebas Neue",Impact,sans-serif;font-weight:400;font-size:104px;line-height:100px;color:var(--navy);letter-spacing:3px}

/* nav */
.nav{left:0;top:800px;width:1200px;height:70px;background:var(--nav);display:flex;padding-left:110px}
.nav a{display:block;height:70px;line-height:70px;padding:0 52px;color:var(--white);font-size:18px;text-decoration:none;letter-spacing:1px}
.nav a.active{background:var(--nav-active);color:var(--nav)}

/* about */
.about-frame{left:132px;top:950px;width:400px;height:540px;background:var(--white);box-shadow:0 2px 10px rgba(0,0,0,.25)}
.about-photo{left:146px;top:964px;width:372px;height:512px;background:linear-gradient(180deg,#b7cde0 0%,#dde6ee 35%,#cfc3b2 62%,#6e6a66 82%,#2f2f33 100%)}
.welcome{left:600px;top:890px;font-family:"Great Vibes",cursive;font-size:80px;line-height:100px;color:var(--navy)}
.about-name{left:600px;top:972px;font-family:"Bebas Neue",Impact,sans-serif;font-weight:400;font-size:76px;line-height:80px;color:var(--navy);letter-spacing:2px}
.about-text{left:600px;top:1062px;width:490px;font-size:14px;line-height:23px}
.about-text p{margin-bottom:20px}

.rule{left:0;width:1200px;height:6px;background:var(--rule)}

.section-title{left:80px;font-family:"Bebas Neue",Impact,sans-serif;font-weight:400;font-size:84px;line-height:90px;color:var(--navy);letter-spacing:2px}

/* gallery */
.thumb{top:1680px;width:232px;height:152px}
.arrow{top:1726px}

/* services */
.circle{top:2040px;width:200px;height:200px;border-radius:50%;border:5px solid var(--navy);padding:5px;background:var(--white)}
.circle span{display:block;width:100%;height:100%;border-radius:50%}
.svc{top:2262px;width:260px;text-align:center}
.svc h3{font-weight:400;font-size:26px;color:var(--navy);margin-bottom:12px}
.svc p{font-size:14px;line-height:22px}
.svc .note{color:var(--accent)}
.extensions{left:0;top:2568px;width:1200px;text-align:center;font-weight:600;font-size:26px;color:var(--navy)}

/* contact */
.contact-text{left:80px;top:2780px;width:460px;font-size:16px;line-height:27px}
.contact-line{display:flex;align-items:center;gap:14px;margin-top:8px}
.social{display:flex;gap:24px;margin-top:20px}
.social span{width:46px;height:46px;background:var(--navy);border-radius:4px}
.field{position:absolute;height:44px;border:2px solid var(--field);font-size:14px;padding:0 14px;line-height:40px;color:#8a93a0;background:var(--white)}
.submit{left:600px;top:3028px;width:150px;height:50px;background:var(--navy);color:var(--white);font-weight:700;font-size:18px;letter-spacing:1px;text-align:center;line-height:50px}

/* map & footer */
.map{left:0;top:3120px;width:1200px;height:280px;background:linear-gradient(160deg,#ebe6d6 0%,#dfe3cf 35%,#c8dbe2 60%,#a9c9e3 100%)}
.footer{left:0;top:3400px;width:1200px;height:112px;background:var(--nav);color:var(--white);text-align:center}
.footer nav{padding-top:24px;font-size:16px}
.footer nav a{color:var(--white);text-decoration:none;margin:0 26px;letter-spacing:1px}
.footer p{margin-top:20px;font-size:14px}
</style>
</head>
<body>

<header>
  <div class="abs hero"></div>
  <div class="abs hero-boards"></div>
  <div class="abs hero-photo" role="img" aria-label="Bride in a strapless lace gown holding a red bouquet, against whitewashed wooden boards"></div>
  <div class="abs hero-ribbon" role="img" aria-label="Purple satin ribbon draped across the boards"></div>
  <div class="abs brand">Brightcomb</div>
  <h1 class="abs hero-title">Chic<br>Sophisticate<br>Dinspired</h1>
</header>

<nav class="abs nav">
  <a class="active" href="#about">ABOUT</a>
  <a href="#gallery">GALLERY</a>
  <a href="#services">SERVICES</a>
  <a href="#contact">CONTACT</a>
</nav>

<section id="about">
  <div class="abs about-frame"></div>
  <div class="abs about-photo" role="img" aria-label="Bride and groom embracing on a beach pier at sunset"></div>
  <div class="abs welcome">Welcome</div>
  <h2 class="abs about-name">BRIGHTCOMB</h2>
  <div class="abs about-text">
    <p>Brightcomb Studio specializes in providing gorgeous, long lasting hair and makeup. With years of experience and training, we know how to make your day the very best. We take pride in client satisfaction and in helping you achieve the look of your dreams. Our team works on location so you can relax with the people you love, and we use only quality products so your look stays flawless all night long.</p>
    <p>If your needs are more professional, we have you covered! We also offer airbrush makeup for film, photo shoots and runway, and our stylists specialize in cut, color and extensions.</p>
    <p>We also provide services in studio and are happy to meet all of your hair care needs.</p>
  </div>
</section>

<div class="abs rule" style="top:1540px"></div>

<section id="gallery">
  <h2 class="abs section-title" style="top:1570px">Gallery</h2>
  <svg class="abs arrow" style="left:40px" width="24" height="60" viewBox="0 0 24 60"><path d="M20 4 L4 30 L20 56" fill="none" stroke="#0d2f5a" stroke-width="4"/></svg>
  <div class="abs thumb" style="left:80px;background:linear-gradient(135deg,#e9e4dc,#b79a7e)" role="img" aria-label="Stylist arranging a bride's hair"></div>
  <div class="abs thumb" style="left:350px;background:linear-gradient(135deg,#d7d2cc,#8c7a6a)" role="img" aria-label="Bride with a braided updo"></div>
  <div class="abs thumb" style="left:620px;background:linear-gradient(135deg,#d0d0d0,#3c3c3c)" role="img" aria-label="Black and white photo of a wedding party"></div>
  <div class="abs thumb" style="left:888px;background:linear-gradient(135deg,#bcd3e6,#e6dccd)" role="img" aria-label="Couple on the beach at the waterline"></div>
  <svg class="abs arrow" style="left:1136px" width="24" height="60" viewBox="0 0 24 60"><path d="M4 4 L20 30 L4 56" fill="none" stroke="#0d2f5a" stroke-width="4"/></svg>
</section>

<div class="abs rule" style="top:1908px"></div>

<section id="services">
  <h2 class="abs section-title" style="top:1932px">Our Services</h2>

  <div class="abs circle" style="left:108px"><span style="background:linear-gradient(135deg,#e2d6c8,#9c7d62)" role="img" aria-label="Bride with a soft curled updo"></span></div>
  <div class="abs circle" style="left:372px"><span style="background:linear-gradient(135deg,#d9b58a,#7a5236)" role="img" aria-label="Woman with long layered blonde hair"></span></div>
  <div class="abs circle" style="left:620px"><span style="background:linear-gradient(135deg,#e0a06a,#8e4420)" role="img" aria-label="Woman with copper red wavy hair"></span></div>
  <div class="abs circle" style="left:888px"><span style="background:linear-gradient(135deg,#d4c4b3,#6e5646)" role="img" aria-label="Woman with a sleek styled blowout"></span></div>

  <div class="abs svc" style="left:78px"><h3>Bridal</h3><p>Thank you for your interest in our on location bridal services. Please contact us for more information.</p></div>
  <div class="abs svc" style="left:342px"><h3>Hair Cut</h3><p>Women $35<br>Men $18</p></div>
  <div class="abs svc" style="left:590px"><h3>Color</h3><p>Partial Highlights $130+<br>Full Highlights $165+<br>Double Process $155+<br>Ombré $125+<br>Roots with Glaze $110+<br>All Over Color $120+<br><span class="note">All color services include a complimentary hair cut and blowout</span></p></div>
  <div class="abs svc" style="left:858px"><h3>Styling &amp; Treatments</h3><p>Blow-out/Hair Styling $35<br>Event Updo $85<br>Deep Condition $15<br>Keratin Smoothing Treatment $150+</p></div>

  <div class="abs extensions">Hair Extensions – Complimentary Consultation</div>
</section>

<div class="abs rule" style="top:2640px"></div>

<section id="contact">
  <h2 class="abs section-title" style="top:2662px">Contact Us</h2>
  <div class="abs contact-text">
    <p>Have a question, desire more information, or just want to have a chat?</p>
    <p style="margin-top:12px">Please contact us:</p>
    <div class="contact-line">
      <svg width="24" height="24" viewBox="0 0 24 24"><path d="M6.6 10.8a15 15 0 0 0 6.6 6.6l2.2-2.2c.3-.3.7-.4 1-.2 1.1.4 2.3.6 3.6.6.6 0 1 .4 1 1V20c0 .6-.4 1-1 1A17 17 0 0 1 3 4c0-.6.4-1 1-1h3.5c.6 0 1 .4 1 1 0 1.3.2 2.5.6 3.6.1.3 0 .7-.2 1z" fill="#0d2f5a"/></svg>
      <span>843.555.0147</span>
    </div>
    <div class="contact-line">
      <svg width="24" height="24" viewBox="0 0 24 24"><rect x="2" y="5" width="20" height="14" rx="2" fill="none" stroke="#0d2f5a" stroke-width="2"/><path d="M2 6l10 7 10-7" fill="none" stroke="#0d2f5a" stroke-width="2"/></svg>
      <span>hello@brightcombstudio-example.com</span>
    </div>
    <p style="margin-top:14px">We look forward to hearing from you!</p>
    <div class="social"><span></span><span></span><span></span></div>
  </div>

  <div class="field" style="left:600px;top:2780px;width:248px">Enter Name</div>
  <div class="field" style="left:872px;top:2780px;width:248px">Enter Email</div>
  <div class="field" style="left:600px;top:2840px;width:248px">Enter Contact No.</div>
  <div class="field" style="left:872px;top:2840px;width:248px">Enter Subject</div>
  <div class="field" style="left:600px;top:2900px;width:520px;height:110px">Message</div>
  <div class="abs submit">SUBMIT</div>
</section>

<div class="abs map" role="img" aria-label="Street map of the Charleston harbor area"></div>

<footer class="abs footer">
  <nav><a href="#">HOME</a><a href="#about">ABOUT</a><a href="#gallery">GALLERY</a><a href="#services">SERVICES</a><a href="#contact">CONTACT</a></nav>
  <p>© <strong>Brightcomb Studio</strong>, 2015. All Rights Reserved.</p>
</footer>

</body>
</html>
```